Alloy wheel repair business needs a website

Install logo previously purchased from makerhive, toolbar with dropdowns. services, gallery, clients , contact ect
Maybe mission statment

Target Market(s)

vehicle owners, auto dealers,insurance companies,

Industry/Entity Type

Alloy Wheel Repair

Coding

Coded - Design and coding required

Number of Pages Required

4 page

Font styles to use
Sans Serif

Colors
0054AA
0677BA
7BADD7
CADEEF
E8F1F8

```html
<!DOCTYPE html>
<html lang="en">
<head>
<meta charset="utf-8">
<title>Rimcraft Works — Alloy Wheel Repair</title>
<link href="https://fonts.googleapis.com/css2?family=Michroma&family=Montserrat:wght@600;700&family=Lato:wght@400;700&display=swap" rel="stylesheet">
<style>
:root{
  --blue:#4a8fd2;
  --blue-deep:#0677BA;
  --blue-soft:#7BADD7;
  --blue-pale:#CADEEF;
  --blue-mist:#E8F1F8;
  --navy:#1c3f73;
  --red:#e3202b;
  --ink:#111;
  --text:#333;
  --white:#fff;
  --black:#0a0a0a;
}
*{margin:0;padding:0;box-sizing:border-box}
html,body{width:1200px;height:4063px;overflow:hidden;background:var(--white)}
body{position:relative;font-family:'Lato',sans-serif;color:var(--text)}
.abs{position:absolute}
.display{font-family:'Michroma',sans-serif;font-weight:400;letter-spacing:1px}

/* header */
.site-header{left:0;top:0;width:1200px;height:87px;background:var(--white)}
.brand{font-family:'Michroma',sans-serif;color:var(--navy);line-height:1}
.header-brand{left:112px;top:16px;display:flex;align-items:center;gap:10px}
.header-brand .mark{width:22px;height:22px;border-radius:50%;background:var(--blue)}
.header-brand .name{font-size:21px;letter-spacing:2px}
.main-nav{left:537px;top:22px;height:41px;display:flex;align-items:center;font-family:'Michroma',sans-serif;font-size:12px;color:#222}
.main-nav a{color:inherit;text-decoration:none;margin-right:42px}
.main-nav a.active{color:var(--blue)}
.main-nav .nav-cta{background:var(--blue);color:var(--white);padding:13px 14px;border-radius:8px 0 8px 0;margin-right:0}

/* hero */
.hero{left:0;top:87px;width:1200px;height:507px;background:linear-gradient(90deg,#0b0b0c 0%,#1a1b1d 40%,#3a3d42 62%,#202225 80%,#0e0f10 100%)}
.hero-wheel{left:560px;top:0;width:640px;height:507px;background:radial-gradient(circle at 215px 260px,#3c3f44 0,#23252a 120px,#111214 230px,rgba(0,0,0,0) 330px)}
.hero-kicker{left:110px;top:182px;color:var(--white);font-size:17px}
.hero-title{left:110px;top:216px;color:var(--white);font-size:38px;letter-spacing:1px}
.hero-copy{left:110px;top:273px;width:450px;color:var(--white);font-size:14px;line-height:28px}
.btn{display:flex;align-items:center;justify-content:center;text-decoration:none;color:var(--white);border-radius:10px 0 10px 0;box-shadow:4px 4px 0 rgba(255,255,255,.55)}
.hero-btn{left:110px;top:375px;width:180px;height:54px;background:var(--blue);font-family:'Michroma',sans-serif;font-size:15px}
.slider-dots{left:112px;top:470px;display:flex;gap:6px}
.slider-dots span{width:37px;height:6px;border-radius:3px;background:#555}
.slider-dots span.on{background:var(--white)}

/* about */
.section-title{left:0;width:1200px;text-align:center;font-size:37px;color:var(--ink)}
.section-title em{font-style:normal;color:var(--blue)}
.about-title{top:648px}
.about-copy{left:140px;width:920px;text-align:center;font-size:14px;line-height:28px;color:#222}
.btn-red{left:509px;top:937px;width:180px;height:54px;background:var(--red);font-family:'Montserrat',sans-serif;font-weight:700;font-size:19px;box-shadow:4px 4px 0 #c8c8c8}
.about-band{left:0;top:1033px;width:1200px;height:415px;background:linear-gradient(180deg,#fff 0%,#d9dadd 22%,#8e9196 55%,#4b4d52 85%,#2e2f33 100%)}

/* services */
.services-title{top:1506px}
.service-photo{width:490px;height:368px}
.service-text{width:432px}
.service-text h3{font-family:'Montserrat',sans-serif;font-weight:700;font-size:31px;color:var(--ink);margin-bottom:14px}
.service-text p{font-size:14px;line-height:26px;text-align:justify;color:#222;margin-bottom:24px}
.btn-blue{width:150px;height:47px;background:var(--blue);font-family:'Montserrat',sans-serif;font-weight:700;font-size:16px;box-shadow:4px 4px 0 #cfcfcf}

/* gallery */
.gallery-title{top:2795px}
.gallery-tile{height:204px}

/* footer */
.site-footer{left:0;top:3440px;width:1200px;height:548px;background:var(--black)}
.contact-card{left:109px;top:3379px;width:388px;height:532px;background:var(--white);border:3px solid var(--blue)}
.contact-card h2{position:absolute;left:0;top:42px;width:100%;text-align:center;font-size:31px;color:var(--ink)}
.contact-card h2 em{font-style:normal;color:var(--blue)}
.field{position:absolute;left:17px;width:348px;height:66px;border:2px solid #d6d6d6;border-radius:12px;padding:22px 20px;font-family:'Montserrat',sans-serif;font-weight:600;font-size:14px;color:#333}
.submit{left:96px;top:444px;width:180px;height:56px;background:var(--blue);font-family:'Montserrat',sans-serif;font-weight:700;font-size:19px;box-shadow:4px 4px 0 #cfcfcf}
.footer-brand{left:577px;top:3563px;display:flex;align-items:center;gap:10px;color:var(--white)}
.footer-brand .mark{width:24px;height:24px;border-radius:50%;background:var(--white)}
.footer-brand .name{font-size:24px;letter-spacing:2px;color:var(--white)}
.footer-copy{left:577px;top:3641px;width:515px;color:var(--white);font-size:14px;line-height:28px}
.contact-item{display:flex;align-items:flex-start;gap:14px;color:var(--white);font-size:14px;line-height:27px}
.contact-item svg{flex:none}
.copyright{left:0;top:3988px;width:1200px;height:75px;background:var(--blue);color:var(--white);font-weight:700;font-size:14px;display:flex;align-items:center;justify-content:center}
</style>
</head>
<body>

<header class="abs site-header">
  <div class="abs header-brand"><span class="mark"></span><span class="brand name">RIMCRAFT WORKS</span></div>
  <nav class="abs main-nav">
    <a class="active" href="#">HOME</a>
    <a href="#">CLIENTS</a>
    <a href="#">SERVICES</a>
    <a href="#">GALLERY</a>
    <a class="nav-cta" href="#">CONTACT US</a>
  </nav>
</header>

<section class="abs hero">
  <div class="abs hero-wheel" role="img" aria-label="Close-up of a black alloy wheel with red brake caliper on a dark car"></div>
  <p class="abs display hero-kicker" style="top:95px">WELCOME TO</p>
  <h1 class="abs display hero-title" style="top:128px">RIMCRAFT WORKS</h1>
  <p class="abs hero-copy" style="top:186px">Itaque earum rerum hic tenetur a sapiente delectus, ut aut reiciendis voluptatibus maiores alias consequatur aut perferendis doloribus asperiores repellat.</p>
  <a class="abs btn hero-btn" style="top:288px" href="#">GET STARTED</a>
  <div class="abs slider-dots" style="top:383px"><span class="on"></span><span></span><span></span></div>
</section>

<h2 class="abs display section-title about-title">ABOUT <em>RIMCRAFT WORKS</em></h2>
<p class="abs about-copy" style="top:713px">Excepturi sint occaecati cupiditate non provident, similique sunt in culpa qui officia deserunt mollitia animi, id est laborum et dolorum fuga. Et harum quidem rerum facilis est et expedita distinctio.Nam libero tempore, cum soluta nobis est eligendi optio cumque nihil impedit quo minus id quod maxime placeat facere possimus, omnis voluptas assumenda est, omnis dolor repellendus.</p>
<p class="abs about-copy" style="top:825px">Temporibus autem quibusdam et aut officiis debitis aut rerum necessitatibus saepe eveniet ut et voluptates repudiandae sint et molestiae non recusandae. Itaque earum rerum hic tenetur a sapiente delectus, ut aut reiciendis voluptatibus maiores alias consequatur aut perferendis doloribus asperiores repellat.</p>
<a class="abs btn btn-red" href="#">READ MORE</a>
<div class="abs about-band" role="img" aria-label="Silver car with a polished multi-spoke alloy wheel"></div>

<h2 class="abs display section-title services-title">OUR <em>SERVICES</em></h2>

<div class="abs service-photo" style="left:110px;top:1607px;background:linear-gradient(135deg,#2a2c30,#6d7178 55%,#b7bbc1)" role="img" aria-label="Grey car wheel with silver spokes"></div>
<div class="abs service-text" style="left:658px;top:1653px">
  <h3>Itaque earum rerum</h3>
  <p>Temporibus autem quibusdam et aut officiis debitis aut rerum ndae sint et molestiae non recusandae.</p>
  <p>Itaque earum rerum hic tenetur a sapiente delectus, ut aut reiciendis voluptatibus maiores alias consequatur aut perferendis doloribus asperiores repellat.</p>
  <a class="btn btn-blue" href="#">READ MORE</a>
</div>

<div class="abs service-text" style="left:110px;top:2022px">
  <h3>Temporibus autem</h3>
  <p style="text-align:left">At vero eos et accusamus et iusto odio dignissimos ducimus qui blanditiis praesentium voluptatum deleniti atque corrupti quos dolores et quas molestias excepturi</p>
  <p style="text-align:left">Sint occaecati cupiditate non provident, similique sunt in culpa qui officiad est laborum et dolorum fuga.</p>
  <a class="btn btn-blue" href="#">READ MORE</a>
</div>
<div class="abs service-photo" style="left:601px;top:1974px;width:488px;background:linear-gradient(135deg,#4b5a6e,#2a3342 50%,#7d8a9c)" role="img" aria-label="Dark wheel on a wet blue-grey car"></div>

<div class="abs service-photo" style="left:110px;top:2343px;background:radial-gradient(circle at 140px 180px,#2d2f33,#141518 55%,#6b4a22 80%,#c1762a)" role="img" aria-label="Black alloy wheel with orange brake caliper"></div>
<div class="abs service-text" style="left:656px;top:2390px">
  <h3>Nam libero tempore</h3>
  <p style="text-align:left">Similique sunt in culpa qui officia deserunt mollitia animi, id est laborum et dolorum fuga. Et harum quidem rerum facilis est et expedita distinctio.</p>
  <p style="text-align:left">Nam libero tempore, cum soluta nobis est eligendi optio cumque nihil impedit quo minus id quod maxime placeat facere.</p>
  <a class="btn btn-blue" href="#">READ MORE</a>
</div>

<h2 class="abs display section-title gallery-title">OUR <em>GALLERY</em></h2>
<div class="abs gallery-tile" style="left:6px;top:2879px;width:288px;background:linear-gradient(135deg,#b3161e,#1b1c1f 45%,#8a8c90)" role="img" aria-label="Sports car wheel with red caliper"></div>
<div class="abs gallery-tile" style="left:6px;top:3095px;width:288px;background:linear-gradient(180deg,#6f7f5a,#3a4a3e 45%,#1d2c4c 70%,#8f8a80)" role="img" aria-label="Classic blue coupe in front of a house"></div>
<div class="abs" style="left:303px;top:2879px;width:289px;height:418px;background:linear-gradient(135deg,#5d94cf,#4a86c6 60%,#3f7bbd)" role="img" aria-label="Blue-tinted alloy wheel close-up"></div>
<div class="abs" style="left:604px;top:2879px;width:289px;height:418px;background:linear-gradient(180deg,#5a6d86,#a5adb8 35%,#d7d8da 55%,#9d8c78 85%,#6c5b48)" role="img" aria-label="White SUV parked by a modern building"></div>
<div class="abs gallery-tile" style="left:905px;top:2879px;width:289px;background:linear-gradient(180deg,#8d96a3,#c2b8a7 45%,#9a7c5c 75%,#b4977a)" role="img" aria-label="Black SUV in a desert landscape"></div>
<div class="abs gallery-tile" style="left:905px;top:3095px;width:289px;background:radial-gradient(circle at 145px 110px,#2c2d30,#0f1012 60%,#55575c)" role="img" aria-label="Tyre standing in a workshop"></div>

<footer class="abs site-footer"></footer>

<form class="abs contact-card">
  <h2 class="display">CONTACT <em>US</em></h2>
  <div class="field" style="top:81px">Name</div>
  <div class="field" style="top:160px">Email</div>
  <div class="field" style="top:236px">Phone Number</div>
  <div class="field" style="top:313px;height:110px">Message</div>
  <a class="abs btn submit" href="#">SUBMIT</a>
</form>

<div class="abs footer-brand"><span class="mark"></span><span class="brand name">RIMCRAFT WORKS</span></div>
<p class="abs footer-copy">Temporibus autem quibusdam et aut officiis debitis aut rerum necessitatibus saepe eveniet ut et voluptates repudiandae sint et molestiae non recu sandae. Itaque earum rerum hic tenetur a sapiente delectus, ut aut reiciendis voluptatibus consequatur aut permaiores alias consequatur aut perferendis doloribus asperiores repellat.</p>

<div class="abs contact-item" style="left:577px;top:3797px">
  <svg width="30" height="30" viewBox="0 0 30 30"><circle cx="15" cy="15" r="15" fill="#fff"/><path d="M15 7a5.5 5.5 0 0 0-5.5 5.5c0 4 5.5 10 5.5 10s5.5-6 5.5-10A5.5 5.5 0 0 0 15 7zm0 7.5a2 2 0 1 1 0-4 2 2 0 0 1 0 4z" fill="#000"/></svg>
  <span>Rimcraft Works<br>United States</span>
</div>
<div class="abs contact-item" style="left:923px;top:3797px;align-items:center">
  <svg width="32" height="32" viewBox="0 0 32 32"><circle cx="16" cy="16" r="16" fill="#fff"/><path d="M11.5 9l2.5 0 1.2 3.5-1.6 1.3a9 9 0 0 0 4.6 4.6l1.3-1.6 3.5 1.2v2.5a1.6 1.6 0 0 1-1.7 1.5C14.6 21.6 10.4 17.4 10 12.7A1.6 1.6 0 0 1 11.5 9z" fill="#000"/></svg>
  <span>+1 555 014 2290</span>
</div>
<div class="abs contact-item" style="left:577px;top:3866px;align-items:center">
  <svg width="30" height="30" viewBox="0 0 30 30"><circle cx="15" cy="15" r="15" fill="#fff"/><rect x="8" y="10" width="14" height="10" rx="1.5" fill="#000"/><path d="M8.5 10.8 15 15.5l6.5-4.7" stroke="#fff" stroke-width="1.3" fill="none"/></svg>
  <span>info@rimcraftworks.com</span>
</div>

<div class="abs copyright">Copyrights@2023.Rimcraft Works.All Rights Reserved</div>

</body>
</html>
```